Birchline Septic Solutions

Would like to see some single sided ones but would also like to see some double sided with one sided only being the logo. Owners name is Colin Vandro. Phone number is 555-214-0387
Services are pumping, inspections, installs, and repairs

Contact Information for Business Card

555-241-0387 Colin Vandro Fernbrook, OH

```html
<!DOCTYPE html>
<html lang="en">
<head>
<meta charset="utf-8">
<title>Birchline Septic Solutions — Business Card</title>
<link rel="stylesheet" href="https://fonts.googleapis.com/css2?family=Open+Sans:wght@400;600;700&display=swap">
<style>
  :root {
    --backdrop: #232323;
    --teal: #27bfb9;
    --teal-soft: #9fe0d0;
    --teal-deep: #1f8f8a;
    --charcoal: #1d1d20;
    --charcoal-lift: #262629;
    --charcoal-mid: #222225;
    --white: #ffffff;
    --muted: #e6e6e6;
  }
  * { box-sizing: border-box; margin: 0; padding: 0; }
  html, body {
    width: 1200px; height: 779px; overflow: hidden;
    background: var(--backdrop);
    font-family: "Open Sans", Arial, sans-serif;
  }
  .stage {
    position: relative; width: 1200px; height: 779px;
    display: flex; justify-content: center; align-items: center; gap: 70px;
  }
  .card {
    position: relative; width: 320px; height: 560px;
    border-radius: 22px; overflow: hidden;
    box-shadow: 0 18px 40px rgba(0,0,0,.55);
  }

  /* Logo side */
  .card--logo {
    background: var(--teal);
    display: flex; align-items: center; justify-content: center;
  }
  .brand-mark {
    display: flex; flex-direction: column; align-items: center; gap: 14px;
    color: var(--teal-soft); font-weight: 700; text-align: center;
  }
  .brand-mark__dot {
    width: 22px; height: 22px; border-radius: 50%; background: var(--teal-soft);
  }
  .brand-mark__name { font-size: 30px; line-height: 1.15; letter-spacing: 1px; }

  /* Contact side */
  .card--contact { background: var(--charcoal); color: var(--white); }
  .card__bands { position: absolute; inset: 0; }
  .card__content {
    position: relative; height: 100%;
    display: flex; flex-direction: column; align-items: center;
  }
  .brand-name {
    margin-top: 62px; font-weight: 700; font-size: 24px; line-height: 1.2;
    text-align: center; color: var(--white); letter-spacing: .5px;
  }
  .owner {
    margin-top: 70px; font-weight: 700; font-size: 27px; line-height: 1;
  }
  .owner__first { color: var(--teal); }
  .owner__last { color: var(--white); }
  .location { margin-top: 6px; font-size: 14px; color: var(--muted); }
  .phone-icon { margin-top: 12px; }
  .phone { margin-top: 4px; font-size: 20px; letter-spacing: .5px; }

  .services { margin-top: 62px; display: flex; flex-direction: column; align-items: center; }
  .services__tag {
    background: var(--teal); color: var(--white);
    font-size: 13px; font-weight: 600; letter-spacing: .5px;
    padding: 3px 22px; border-radius: 50%;
  }
  .services__arrow { margin-top: 2px; }
  .services__list {
    list-style: none; text-align: center; font-size: 15px; line-height: 1.35;
    color: var(--muted); margin-top: 4px;
  }
</style>
</head>
<body>
<main class="stage">
  <section class="card card--logo" aria-label="Logo side">
    <div class="brand-mark">
      <span class="brand-mark__dot"></span>
      <span class="brand-mark__name">Birchline<br>Septic<br>Solutions</span>
    </div>
  </section>

  <section class="card card--contact" aria-label="Contact side">
    <svg class="card__bands" viewBox="0 0 320 560" preserveAspectRatio="none" aria-hidden="true">
      <path d="M0 0 H320 V455 Q250 360 0 395 Z" fill="#1b1b1e"/>
      <path d="M0 0 H320 V255 Q300 330 150 345 Q60 352 0 340 Z" fill="#262629"/>
      <path d="M320 255 Q300 330 150 345 Q60 352 0 340 V395 Q250 360 320 455 Z" fill="#222225"/>
    </svg>
    <div class="card__content">
      <h1 class="brand-name">Birchline<br>Septic Solutions</h1>
      <p class="owner"><span class="owner__first">Colin</span> <span class="owner__last">Vandro</span></p>
      <p class="location">Fernbrook, OH</p>
      <svg class="phone-icon" width="26" height="34" viewBox="0 0 26 34" aria-hidden="true">
        <circle cx="13" cy="12" r="11" fill="var(--teal)"/>
        <path d="M9 8.5c.8-.6 1.6-.3 2 .5l.6 1.2c.3.6 0 1.1-.5 1.4.5 1.2 1.3 2 2.4 2.5.3-.5.8-.8 1.4-.5l1.2.6c.8.4 1 1.2.4 2-.9 1.1-2.4 1-3.8.2-1.8-1-3.2-2.5-4-4.3-.6-1.4-.6-2.8.3-3.6z" fill="var(--white)"/>
        <path d="M13 24 L13 31 M9 28 L13 32 L17 28" stroke="var(--teal)" stroke-width="2" fill="none"/>
      </svg>
      <p class="phone">555-241-0387</p>

      <div class="services">
        <span class="services__tag">SERVICES</span>
        <svg class="services__arrow" width="14" height="12" viewBox="0 0 14 12" aria-hidden="true">
          <path d="M7 0 V9 M3 6 L7 11 L11 6" stroke="var(--teal)" stroke-width="2" fill="none"/>
        </svg>
        <ul class="services__list">
          <li>Installs</li>
          <li>Pumping</li>
          <li>Inspections</li>
          <li>And Repairs</li>
        </ul>
      </div>
    </div>
  </section>
</main>
</body>
</html>
```